Inspection Company - Commercial Brochure Design

We are looking to finalize our 8 x 11 brochure. We are an industry leader in our space of commercial and home inspections.

We really like the front and back design labeled-

We have made some suggestions for the internal pages-

These are only suggestions for the interior section- The wording should remain the same. The images can be removed / rearranged/ etc. There is full creative freedom for the interior.

Wording for Inside Right Page-
With over 500,000 properties inspected we know how to inspect each building type to maximize a Return On Investment for our clients. . Our Inspectors focus on all the critical building components (structural, roof, electrical, plumbing, air and heating, drainage, etc.), health and safety issues – emergency egress and other potential hazards. We document current condition and any immediate and future repairs that are necessary. When scheduling our team take all details into account building construction type, age, location, and property use into consideration to ensure we are fully prepared to conduct a thorough inspection.

Target Market(s)

Investors- Commercial Real Estate Investors

Industry/Entity Type

Commercial Real Estate Inspections

Requirements
Must have
• Similar branding to our website (https://morvanteq.com/brightcommercial) (https://bravuraassessments.com/) and ( the uploaded documents (Commercial report cover sample.JPG & designcrowd_z6se15j73jk0fe9fc2samkecn7_image (1).jpg )
Nice to have
• Must have Brand Logos and Brand Colors- Nice to have creative ideas of displaying the information

```html
<!DOCTYPE html>
<html lang="en">
<head>
<meta charset="utf-8">
<title>Quorvale Group – Inspection Brochure</title>
<link href="https://fonts.googleapis.com/css2?family=Arimo:wght@400;700&family=Alegreya+Sans:wght@400&display=swap" rel="stylesheet">
<style>
:root{
  --backdrop:#cfcfcf;
  --paper:#ffffff;
  --navy-deep:#0b1f38;
  --navy-mid:#123d66;
  --navy-light:#1b6099;
  --accent-blue:#1a64a8;
  --dash-blue:#1d5f96;
  --panel-grey:#ebebeb;
  --ink:#1f1f1f;
  --frame-edge:#7cc0f0;
}
*{margin:0;padding:0;box-sizing:border-box}
html,body{width:1200px;height:719px;overflow:hidden;background:var(--backdrop)}
body{font-family:'Arimo',Arial,sans-serif;position:relative}
.page{position:absolute;top:23px;height:641px;background:var(--paper);box-shadow:0 14px 18px -8px rgba(20,40,70,.45);overflow:hidden}
.page--left{left:30px;width:497px}
.page--right{left:673px;width:499px}
.header{position:absolute;left:0;top:20px;width:100%;background:linear-gradient(180deg,var(--navy-deep) 0%,var(--navy-mid) 55%,var(--navy-light) 100%)}
.page--left .header{height:153px}
.page--right .header{height:123px}
.brand-mark{position:absolute;left:31px;top:14px;width:58px;height:58px;border:3px solid #fff;border-radius:50%}
.brand-name{position:absolute;left:94px;top:34px;color:#fff;font-weight:700;font-size:15px;letter-spacing:.5px}
.page-title{position:absolute;left:94px;top:58px;color:#fff;font-size:19px;font-weight:400;letter-spacing:.2px}
.footer{position:absolute;left:0;bottom:0;width:100%;height:149px;background:linear-gradient(180deg,var(--navy-deep) 0%,var(--navy-mid) 50%,var(--navy-light) 100%)}
.site-url{position:absolute;right:33px;bottom:20px;color:#fff;font-family:'Alegreya Sans',sans-serif;font-size:14px;letter-spacing:1.2px}
.photo{position:absolute;width:117px;height:103px;border-radius:16px;box-shadow:-5px 4px 6px rgba(0,0,0,.25);border-top:3px solid var(--frame-edge);border-left:3px solid var(--frame-edge)}
.photo-thermal{background:linear-gradient(135deg,#8f8f8f,#3b3b3b 55%,#c9b49a)}
.photo-roof{background:linear-gradient(180deg,#6e7680,#c9cdd2 45%,#e3e4e6)}
.photo-wall{background:linear-gradient(180deg,#d8d8d8,#a8a8a4 65%,#58763b)}
.photo-ada{background:linear-gradient(135deg,#e6eaee,#9aa1a8 50%,#2a2a2a)}
.photo-roofcert{background:linear-gradient(135deg,#1c1c22,#3a3440 50%,#e7c7cf)}
.photo-mold{background:linear-gradient(180deg,#9fb3be,#f1f1f1 55%,#c97a7a)}
.photo-sewer{background:linear-gradient(135deg,#b9262b,#2a2a2a 55%,#8a8a8a)}
.photo-termite{background:linear-gradient(180deg,#9a5a44,#c7a887 50%,#e0cfb2)}
.check-panel{position:absolute;top:340px;width:137px;height:110px;background:var(--panel-grey);border-radius:6px}
.check-list{position:absolute;list-style:none;font-size:11px;line-height:17px;color:var(--ink)}
.check-list li{position:relative}
.check-list li.item::before{content:"";position:absolute;left:-19px;top:7px;width:15px;height:3px;background:var(--dash-blue)}
.service-label{position:absolute;width:130px;text-align:center;color:var(--accent-blue);font-size:11px;line-height:13.5px}
.badge{position:absolute}
.badge-round{left:217px;top:11px;width:92px;height:92px;border-radius:50%;background:#fff;border:5px solid #c8232c;box-shadow:inset 0 0 0 6px #1e3a78}
.badge-cert{left:337px;top:20px;width:133px;height:62px}
.badge-cert .seal{position:absolute;left:0;top:0;width:62px;height:62px;border-radius:50%;background:#1d3f7a;border:3px solid #c9a640}
.badge-cert .plate{position:absolute;left:52px;top:8px;width:81px;height:45px;background:#1d3f7a;border:2px solid #c9a640}
</style>
</head>
<body>

<section class="page page--left">
  <header class="header">
    <div class="brand-mark"></div>
    <div class="brand-name">QUORVALE GROUP</div>
    <h1 class="page-title">WHAT WE INSPECT</h1>
  </header>

  <div class="photo photo-thermal" style="left:32px;top:211px" role="img" aria-label="Inspector using a thermal camera on plumbing"></div>
  <div class="photo photo-roof" style="left:188px;top:211px" role="img" aria-label="Flat commercial roof with skylights"></div>
  <div class="photo photo-wall" style="left:343px;top:211px" role="img" aria-label="Concrete block foundation wall"></div>

  <div class="check-panel" style="left:23px"></div>
  <div class="check-panel" style="left:180px"></div>
  <div class="check-panel" style="left:337px;top:339px"></div>

  <ul class="check-list" style="left:35px;top:346px">
    <li class="item">LEAKS</li>
    <li class="item">TYPE</li>
    <li class="item">MOISTURE INTRUSION</li>
  </ul>
  <ul class="check-list" style="left:196px;top:347px">
    <li class="item">LEAKS</li>
    <li class="item">SEALS</li>
    <li class="item">SURFACE MATERIAL</li>
    <li>CONDITION</li>
    <li class="item">&nbsp;AGE AND REMAINING</li>
    <li>&nbsp;USEFUL&nbsp; LIFE</li>
  </ul>
  <ul class="check-list" style="left:363px;top:331px">
    <li>CRACKS</li>
    <li class="item" style="margin-top:5px">STRUCTURAL</li>
    <li class="item">INSTALLATION</li>
    <li class="item">CONCRETE</li>
    <li class="item">STEEL AND WOOD</li>
    <li>COMPONENTS</li>
  </ul>

  <footer class="footer">
    <div class="site-url">MORVANTEQ.COM</div>
  </footer>
</section>

<section class="page page--right">
  <header class="header">
    <div class="brand-mark"></div>
    <div class="brand-name">QUORVALE GROUP</div>
    <h1 class="page-title">ADDITIONAL SERVICES&nbsp; AVAILABLE</h1>
  </header>

  <div class="photo photo-ada" style="left:32px;top:159px" role="img" aria-label="Calculator and financial documents"></div>
  <div class="photo photo-roofcert" style="left:188px;top:159px" role="img" aria-label="Signing a certification document"></div>
  <div class="photo photo-mold" style="left:345px;top:159px" role="img" aria-label="Laboratory analysis"></div>

  <div class="service-label" style="left:25px;top:277px">ADA COMPLIANCE<br>INSPECTIONS</div>
  <div class="service-label" style="left:180px;top:269px">ROOF<br>CERTIFICATION AND<br>MAINTENANCE -<br>LICENSED ROOFER</div>
  <div class="service-label" style="left:335px;top:269px">MOLD AND<br>MOISTURE ANALYSIS<br>FROM CERTIFIED<br>MOLD EXPERT</div>

  <div class="photo photo-sewer" style="left:111px;top:342px" role="img" aria-label="Sewer inspection camera monitor"></div>
  <div class="photo photo-termite" style="left:268px;top:342px" role="img" aria-label="Crawlspace termite inspection"></div>

  <div class="service-label" style="left:104px;top:452px">SEWER CAMERA<br>INSPECTIONS</div>
  <div class="service-label" style="left:260px;top:452px">TERMITE<br>INSPECTIONS</div>

  <footer class="footer">
    <div class="badge badge-round" role="img" aria-label="Discount program badge"></div>
    <div class="badge badge-cert" role="img" aria-label="Certification badge">
      <div class="plate"></div>
      <div class="seal"></div>
    </div>
    <div class="site-url">MORVANTEQ.COM</div>
  </footer>
</section>

</body>
</html>
```